Tech business card design

We need an amazing business card design for our new business 'Pexla' a marketing tech startup based in Sydney, Australia. We provide an online marketplace for businesses to search and buy advertising media, connect with service providers and learn more about marketing. We wish to communicate 'cool tech', reliability and professionalism and design based around our logo.

Target Market(s)

Business Owners

Contact Information for Business Card

Name
Position
Email Address
Website
Phone Number

Font styles to use
Other font styles liked:
• Avenir & Avenir Next

Colors

Designer to choose colors to be used in the design.

```html
<!DOCTYPE html>
<html lang="en">
<head>
<meta charset="utf-8">
<title>Pexla Business Card</title>
<link rel="stylesheet" href="https://fonts.googleapis.com/css2?family=Nunito+Sans:wght@400;600;800;900&display=swap">
<style>
  :root {
    --stage: #1e1e1f;
    --navy: #1a1e4c;
    --navy-ink: #151842;
    --white: #ffffff;
    --ring: #8a8b91;
    --mist: #9da1c0;
    --mist-dim: #8d91ad;
  }
  * { box-sizing: border-box; margin: 0; padding: 0; }
  html, body {
    width: 1200px; height: 900px; overflow: hidden;
    background: var(--stage);
    font-family: "Nunito Sans", "Avenir Next", Avenir, sans-serif;
  }
  .card {
    position: absolute;
    width: 540px; height: 310px;
    border-radius: 22px;
    background: var(--navy);
    overflow: hidden;
    box-shadow: 0 14px 30px rgba(0,0,0,0.55);
  }
  .card--front { left: 90px; top: 110px; }
  .card--back  { left: 570px; top: 470px; }

  .front-arc { position: absolute; inset: 0; }
  .front-wordmark {
    position: absolute; left: 40px; top: 112px;
    font-weight: 900; font-size: 88px; letter-spacing: -2px;
    color: var(--navy-ink); line-height: 1;
  }
  .identity {
    position: absolute; right: 28px; top: 26px; text-align: right;
    color: var(--white);
  }
  .identity__name { font-weight: 800; font-size: 17px; letter-spacing: 0.5px; }
  .identity__role { font-weight: 600; font-size: 13px; margin-top: 1px; }

  .contact {
    position: absolute; right: 28px; top: 142px; text-align: right;
    color: var(--white); font-size: 13px; line-height: 1.35;
  }
  .contact__address { margin-bottom: 12px; }
  .contact__row { display: flex; justify-content: flex-end; align-items: center; gap: 7px; margin-top: 5px; }
  .contact__row svg { width: 12px; height: 12px; flex: none; }

  .back-wordmark {
    position: absolute; left: 0; right: 0; top: 82px; text-align: center;
    font-weight: 900; font-size: 120px; letter-spacing: -3px;
    color: var(--mist); line-height: 1;
  }
  .back-web {
    position: absolute; left: 0; right: 0; top: 218px; text-align: center;
    font-size: 14px; letter-spacing: 4px; color: var(--mist-dim);
  }
</style>
</head>
<body>
  <section class="card card--front">
    <svg class="front-arc" viewBox="0 0 540 310" aria-hidden="true">
      <circle cx="182" cy="148" r="172" fill="var(--ring)"/>
      <circle cx="172" cy="146" r="160" fill="var(--white)"/>
    </svg>
    <div class="front-wordmark">Pexla</div>
    <div class="identity">
      <div class="identity__name">JOHN SMITH</div>
      <div class="identity__role">Position</div>
    </div>
    <div class="contact">
      <div class="contact__address">Street Name, City Name<br>Zipcode:012345</div>
      <div class="contact__row">012-345-6789
        <svg viewBox="0 0 24 24"><path fill="#fff" d="M6.6 10.8a15 15 0 0 0 6.6 6.6l2.2-2.2a1 1 0 0 1 1-.25 11.4 11.4 0 0 0 3.6.57 1 1 0 0 1 1 1V20a1 1 0 0 1-1 1A17 17 0 0 1 3 4a1 1 0 0 1 1-1h3.5a1 1 0 0 1 1 1c0 1.25.2 2.45.57 3.57a1 1 0 0 1-.25 1z"/></svg>
      </div>
      <div class="contact__row">info@pexla.com
        <svg viewBox="0 0 24 24"><rect x="2" y="5" width="20" height="14" rx="1" fill="#fff"/><path d="M2 6l10 7 10-7" fill="none" stroke="var(--navy)" stroke-width="2"/></svg>
      </div>
      <div class="contact__row">www.pexla.com
        <svg viewBox="0 0 24 24" fill="none" stroke="#fff" stroke-width="2"><circle cx="12" cy="12" r="9"/><path d="M3 12h18M12 3c3 3.5 3 14.5 0 18M12 3c-3 3.5-3 14.5 0 18"/></svg>
      </div>
    </div>
  </section>

  <section class="card card--back">
    <div class="back-wordmark">Pexla</div>
    <div class="back-web">www.pexla.com</div>
  </section>
</body>
</html>
```